Business Card Design

We are a manufacturing and distribution company with most of our customer base being supermarkets. We have established brand guidelines that are attached.

```html
<!DOCTYPE html>
<html lang="en">
<head>
<meta charset="utf-8">
<title>Valmora Business Card</title>
<link href="https://fonts.googleapis.com/css2?family=Archivo:wght@400;700;800&display=swap" rel="stylesheet">
<style>
  :root {
    --bg: #c4c4c4;
    --card-white: #ffffff;
    --ink: #1b1b1b;
    --brand-red: #e11b22;
    --brand-blue: #1466b3;
    --blue-deep: #0f57a0;
    --grey-text: #333333;
  }
  html, body {
    margin: 0;
    padding: 0;
    width: 1200px;
    height: 788px;
    overflow: hidden;
    background: var(--bg);
    font-family: "Archivo", Arial, sans-serif;
  }
  .stage {
    position: relative;
    width: 1200px;
    height: 788px;
  }
  .card {
    position: absolute;
    top: 244px;
    width: 525px;
    height: 300px;
    border-radius: 22px;
    overflow: hidden;
  }
  .card-front { left: 45px; background: var(--card-white); }
  .card-back { left: 630px; background: var(--brand-blue); }

  .brand {
    position: absolute;
    left: 40px;
    top: 62px;
    display: flex;
    align-items: center;
    gap: 14px;
  }
  .brand-square {
    width: 30px;
    height: 30px;
    background: var(--brand-blue);
  }
  .brand-name {
    font-size: 44px;
    font-weight: 800;
    letter-spacing: 2px;
    color: var(--ink);
    line-height: 1;
  }

  .person {
    position: absolute;
    left: 40px;
    top: 150px;
  }
  .person-name {
    font-size: 25px;
    font-weight: 700;
    letter-spacing: 0.5px;
    line-height: 1;
  }
  .person-name .first { color: var(--brand-red); }
  .person-name .last { color: var(--brand-blue); }
  .person-title {
    margin-top: 6px;
    font-size: 15px;
    color: var(--grey-text);
  }

  .divider {
    position: absolute;
    left: 258px;
    top: 140px;
    width: 2px;
    height: 74px;
    background: var(--brand-red);
  }

  .contacts {
    position: absolute;
    left: 280px;
    top: 140px;
    list-style: none;
    margin: 0;
    padding: 0;
    font-size: 14px;
    color: var(--ink);
  }
  .contacts li {
    display: flex;
    align-items: center;
    gap: 8px;
    height: 25px;
  }
  .contacts svg { width: 13px; height: 13px; flex: none; }

  .bands {
    position: absolute;
    left: 0;
    bottom: 0;
    width: 525px;
    height: 70px;
  }
  .address {
    position: absolute;
    left: 40px;
    bottom: 9px;
    font-size: 14px;
    color: #ffffff;
    letter-spacing: 0.3px;
  }

  .back-pattern {
    position: absolute;
    inset: 0;
    background: linear-gradient(135deg, var(--brand-blue) 0%, var(--blue-deep) 100%);
  }
  .back-brand {
    position: absolute;
    left: 0;
    right: 0;
    top: 50%;
    transform: translateY(-50%);
    text-align: center;
    font-size: 30px;
    font-weight: 800;
    letter-spacing: 2px;
    color: #ffffff;
  }
</style>
</head>
<body>
<main class="stage">
  <section class="card card-front" aria-label="Business card front">
    <div class="brand">
      <span class="brand-square"></span>
      <span class="brand-name">VALMORA</span>
    </div>

    <div class="person">
      <div class="person-name"><span class="first">DANIEL</span> <span class="last">HART</span></div>
      <div class="person-title">CEO/Founder</div>
    </div>

    <div class="divider"></div>

    <ul class="contacts">
      <li>
        <svg viewBox="0 0 16 16"><path fill="#1466b3" d="M3.6 1.5l2.3 2.6-1.3 1.7c.9 2 2.6 3.7 4.6 4.6l1.7-1.3 2.6 2.3-1.5 2.2C6.4 14.5 1.5 9.6 1.4 3z"/></svg>
        555-014-2290
      </li>
      <li>
        <svg viewBox="0 0 16 16"><rect x="1" y="3" width="14" height="10" fill="#1466b3"/><path d="M1 3l7 6 7-6" stroke="#fff" stroke-width="1.3" fill="none"/></svg>
        info@valmora.com.au
      </li>
      <li>
        <svg viewBox="0 0 16 16"><circle cx="8" cy="8" r="7" fill="#1466b3"/><path d="M1 8h14M8 1c-3 3-3 11 0 14M8 1c3 3 3 11 0 14" stroke="#fff" stroke-width="1" fill="none"/></svg>
        www.valmora.com.au
      </li>
    </ul>

    <svg class="bands" viewBox="0 0 525 70" aria-hidden="true">
      <polygon points="0,34 430,34 405,70 0,70" fill="#e11b22"/>
      <polygon points="405,70 430,34 440,34 415,70" fill="#ffffff"/>
      <polygon points="440,20 525,20 525,34 430,34" fill="#1466b3"/>
    </svg>
    <div class="address">2140 Linden Park Road Country Name, AB 40912</div>
  </section>

  <section class="card card-back" aria-label="Business card back">
    <div class="back-pattern" role="img" aria-label="Repeating tonal pattern of the brand mark on blue"></div>
    <div class="back-brand">VALMORA</div>
  </section>
</main>
</body>
</html>
```